Packaged Food Business Needs a Packaging Design

We need a package design to be used as a label/sticker on the lids of round and square transparent plastic containers and on the sides of resealable stand-up pouches. The brand name is 'Savorine' - please find attached logo together with pictures of the sample containers and pouch. We will use the packaging to market a wide variety of food categories from nuts, dried fruits, spices, cooking chocolates, baking ingredients, cereals, grains and pulses.

OVERALL FEEDBACK ON DESIGNS ALREADY RECEIVED:

- We have found so far that a lot of our mandatory requirements are not adhered to in designs that have been submitted so far. We would like to emphasise that the ingredient, weight and expiry text will be printed at the time of packing so it should not take prime space on the pack BUT at the same time some 'blank' space needs to flawlessly be incorporated into the overall design for this purpose
- We encourage you to glorify the brand logo in the pack, and absolutely refrain from duplicating the tagline
- Please note that ONE label design will be used to pack a wide variety of food ingredients and therefore please ensure that the choice of your design incorporates this requirement, in the past we have received designs that are limited to only one type of food (like nuts) or have received designs that are too floral or leafy (and not grounded to food
- Please ensure that you submit designs for all three packaging formats, it is critical to see the family look from the on-set

Target Market(s)

The brand is targeting both mothers and professional chefs and therefore the label design should be broadly approachable and convey affordable premium

Industry/Entity Type

Business

Requirements
Must have
• - Consistent with the brand name and logo, the overall look and feel of the packaging should convey values of healthy, gourmet food ingredients, high in nourishment and project a sense of delightful taste
• - The design styling to be modern and 'simplistic' (embracing 'less-is-more' type of a design style)
• - Design a packaging architecture that incorporates the brand logo together with its tagline lock-up of 'taste the goodness in every spoonful' - find logo attached
• - The design needs to have a dedicated area to print the ingredient (e.g., Mixed Nuts), weight (e.g., 500g) and expiry (this space needs to be flawlessly incorporated into the design) - this information will be printed either with an inkjet printer or with a rubber stamp so please leave an empty space (the text should not be part of the design, just the area for the text needs to be included in the design)
• - The packaging must include 'Packed By: Kestomar Traders Ltd, P. O. Box 51946, Kampala - Uganda'
• - For the design of the resealable pouch, please incorporate a window to see through the ingredients and a hole on top to hang on supermarket pegs if necessary
Nice to have
• - We would love to have some design submissions that are bold and cheerful and fun (but not frivolous) - please see attached inspiration for 'fun' packaging. The attachments are purely for inspiration, not to infringe on anyone else's TM and copyrights
• - Incorporate green to convey healthy, organic values
• - Explore use of gold and silver convey premiumness
Should not have
• - Do not duplicate the tagline
• - Do not include the ingredient, weight and expiry in the main graphic of the design, these will be printed at the time of packing so ensure there is provision for this in a flawless way in the design (e.g., via a blank space allocated for this purpose)

```html
<!DOCTYPE html>
<html lang="en">
<head>
<meta charset="utf-8">
<title>Savorine packaging labels</title>
<link href="https://fonts.googleapis.com/css2?family=Oswald:wght@400;600&family=Poppins:wght@700&display=swap" rel="stylesheet">
<style>
  :root {
    --brand-brown: #3d2410;
    --leaf-green: #6aa534;
    --tab-red: #e35d5d;
    --tab-ink: #c54343;
    --window-grey: #5e5e5e;
    --outline: #8a8a8a;
    --paper: #ffffff;
    --floral-teal: #27b0c4;
    --floral-red: #e85a5a;
    --floral-yellow: #f2b630;
    --floral-green: #3e8e4f;
    --floral-violet: #8a6bb8;
  }
  * { box-sizing: border-box; margin: 0; padding: 0; }
  html, body { width: 1200px; height: 1200px; overflow: hidden; background: var(--paper); }
  body { position: relative; font-family: "Oswald", sans-serif; }

  .floral-band {
    position: absolute;
    background: linear-gradient(115deg, var(--floral-teal) 0%, var(--floral-red) 30%, var(--floral-yellow) 52%, var(--floral-violet) 72%, var(--floral-green) 100%);
    opacity: 0.85;
  }

  .print-tab {
    position: absolute;
    background: var(--tab-red);
    color: var(--tab-ink);
    font-family: "Oswald", sans-serif;
    font-weight: 400;
    text-transform: uppercase;
    display: flex;
    align-items: center;
    justify-content: space-around;
  }
  .print-tab--stacked { flex-direction: column; }
  .print-tab--split span + span { border-left: 1px solid var(--tab-ink); padding-left: 6px; }

  .lockup { position: absolute; text-align: center; color: var(--brand-brown); }
  .brand-name {
    display: block;
    font-family: "Oswald", sans-serif;
    font-weight: 600;
    text-transform: uppercase;
    line-height: 1;
    color: var(--brand-brown);
  }
  .tagline {
    display: block;
    font-family: "Poppins", sans-serif;
    font-weight: 700;
    text-transform: uppercase;
    line-height: 1.2;
    color: var(--leaf-green);
    white-space: nowrap;
  }
  .packed-by {
    display: block;
    font-family: "Oswald", sans-serif;
    font-weight: 600;
    text-transform: uppercase;
    line-height: 1.2;
    white-space: nowrap;
  }
  .packed-by small { font-weight: 400; font-size: 0.5em; letter-spacing: 0; }

  /* Round lid label */
  .lid-label {
    position: absolute; left: 77px; top: 198px; width: 400px; height: 400px;
    border-radius: 50%; border: 1px solid var(--outline); overflow: hidden; background: var(--paper);
  }
  .lid-label .floral-band--top { left: 0; top: 0; width: 100%; height: 112px; }
  .lid-label .floral-band--bottom { left: 0; top: 303px; width: 100%; height: 97px; }
  .lid-label .print-tab { left: 173px; top: 0; width: 61px; height: 86px; font-size: 9px; padding: 10px 0; }
  .lid-label .lockup { left: 0; width: 100%; top: 190px; }
  .lid-label .brand-name { font-size: 66px; letter-spacing: 0.15em; margin-right: -0.15em; }
  .lid-label .tagline { font-size: 12.5px; letter-spacing: 0.12em; margin-top: 5px; }
  .lid-label .packed-by { font-size: 13px; margin-top: 2px; }

  /* Rectangular lid label */
  .strip-label { position: absolute; left: 26px; top: 660px; width: 468px; height: 303px; }
  .strip-label .floral-band--top { left: 0; top: 0; width: 100%; height: 66px; }
  .strip-label .floral-band--bottom { left: 0; top: 259px; width: 100%; height: 44px; }
  .strip-label .print-tab { left: 331px; top: 0; width: 104px; height: 47px; font-size: 8.5px; }
  .strip-label .lockup { left: 0; width: 100%; top: 146px; }
  .strip-label .brand-name { font-size: 66px; letter-spacing: 0.15em; margin-right: -0.15em; }
  .strip-label .tagline { font-size: 12.5px; letter-spacing: 0.12em; margin-top: 4px; }
  .strip-label .packed-by { font-size: 13px; margin-top: 3px; }

  /* Stand-up pouch */
  .pouch {
    position: absolute; left: 570px; top: 219px; width: 574px; height: 860px;
    border: 1px solid var(--outline); background: var(--paper); overflow: hidden;
  }
  .pouch .floral-band--top { left: 0; top: 0; width: 100%; height: 583px; }
  .pouch .hang-hole { position: absolute; left: 217px; top: 8px; width: 142px; height: 55px; }
  .pouch .see-through-window {
    position: absolute; left: 33px; top: 375px; width: 509px; height: 173px;
    background: var(--window-grey); border-radius: 10px;
  }
  .pouch .print-tab { left: 433px; top: 0; width: 87px; height: 119px; font-size: 11px; padding: 14px 0; }
  .pouch .lockup { left: 0; width: 100%; top: 693px; }
  .pouch .brand-name { font-size: 96px; letter-spacing: 0.14em; margin-right: -0.14em; }
  .pouch .tagline { font-size: 18.5px; letter-spacing: 0.12em; margin-top: 8px; }
  .pouch .packed-by { font-size: 20px; margin-top: 4px; }
  .pouch .packed-by small { font-size: 0.45em; }
</style>
</head>
<body>

  <section class="lid-label" aria-label="Round lid label">
    <div class="floral-band floral-band--top" role="img" aria-label="Colourful floral pattern with flowers, leaves and berries"></div>
    <div class="print-tab print-tab--stacked"><span>Ingredients</span><span>Best before</span></div>
    <div class="lockup">
      <span class="brand-name">Savorine</span>
      <span class="tagline">Taste the goodness in every spoonful!</span>
      <span class="packed-by">Packed by <small>Kestomar Traders Ltd, P. O. Box 51946, Kampala - Uganda</small> Net weight</span>
    </div>
    <div class="floral-band floral-band--bottom" role="img" aria-label="Colourful floral pattern with flowers, leaves and berries"></div>
  </section>

  <section class="strip-label" aria-label="Rectangular lid label">
    <div class="floral-band floral-band--top" role="img" aria-label="Colourful floral pattern with flowers, leaves and berries"></div>
    <div class="print-tab print-tab--split"><span>Ingredients</span><span>Best before</span></div>
    <div class="lockup">
      <span class="brand-name">Savorine</span>
      <span class="tagline">Taste the goodness in every spoonful!</span>
      <span class="packed-by">Packed by <small>Kestomar Traders Ltd, P. O. Box 51946, Kampala - Uganda</small> Net weight</span>
    </div>
    <div class="floral-band floral-band--bottom" role="img" aria-label="Colourful floral pattern with flowers, leaves and berries"></div>
  </section>

  <section class="pouch" aria-label="Stand-up pouch">
    <div class="floral-band floral-band--top" role="img" aria-label="Colourful floral pattern with flowers, leaves, berries and a ladybird"></div>
    <svg class="hang-hole" viewBox="0 0 142 55" aria-hidden="true">
      <path d="M14 14 H56 A15 15 0 0 1 86 14 H128 A14 14 0 0 1 142 28 V41 A14 14 0 0 1 128 55 H14 A14 14 0 0 1 0 41 V28 A14 14 0 0 1 14 14 Z" fill="#5e5e5e"/>
    </svg>
    <div class="print-tab print-tab--stacked"><span>Ingredients</span><span>Best before</span></div>
    <div class="see-through-window" aria-label="Clear window"></div>
    <div class="lockup">
      <span class="brand-name">Savorine</span>
      <span class="tagline">Taste the goodness in every spoonful!</span>
      <span class="packed-by">Packed by <small>Kestomar Traders Ltd, P. O. Box 51946, Kampala - Uganda</small> Net weight</span>
    </div>
  </section>

</body>
</html>
```